Business card design Needed for new logo / Construction business, home extensions and new builds

We need a business card design using our new logo files which i will attach to this project :)

We are a small construction business specialising in home extensions, new builds and property development. We are very ambitious and would appreciate professional and elegant designs for our new business card.

Very serious about using the services on MakerQuarry and recently acquired our new logo from here :)

Please get involved, i will feedback when i can as i am very busy but can respond daily, thanks

Target Market(s)

People that want to build onto their houses, new building developments or adding too their existing property

Industry/Entity Type

Construction

Contact Information for Business Card

Renwick Tolliver Construction, Lionel Ashby (Managing Director), Tel 07822254961, email - info@renwick-tolliver, www.renwick-tolliver.co.uk

Colors

Designer to choose colors to be used in the design.

Requirements
Must have
• I like a deep grey on the back please. A lot of you have provided black from and back, try mixing things up a little. The black looks cool 😎 Thanks

```html
<!DOCTYPE html>
<html lang="en">
<head>
<meta charset="UTF-8">
<title>Renwick Tolliver Construction – Business Card</title>
<link rel="stylesheet" href="https://fonts.googleapis.com/css2?family=Cinzel:wght@500;600&family=Poppins:wght@300;400&display=swap">
<style>
  :root {
    --backdrop: #3a3a3a;
    --card-black: #111111;
    --card-front: #161616;
    --watermark-a: #1e1e1e;
    --watermark-b: #141414;
    --gold: #d9a531;
    --gold-light: #f0c75a;
    --silver: #d6d6d6;
    --silver-dim: #b9b9b9;
  }
  * { margin: 0; padding: 0; box-sizing: border-box; }
  html, body {
    width: 1200px; height: 959px; overflow: hidden;
    background: var(--backdrop);
  }
  .canvas {
    width: 1200px; height: 959px;
    display: flex; flex-direction: column; align-items: center; justify-content: center;
    gap: 40px;
  }
  .card {
    position: relative;
    width: 640px; height: 414px;
    border: 1.5px solid var(--gold);
    box-shadow: 0 14px 30px rgba(0,0,0,.45);
    overflow: hidden;
  }
  .card--front { background: var(--card-front); }
  .card--back { background: var(--card-black); }

  .watermark {
    position: absolute; left: 40px; top: 60px;
    width: 360px; height: 320px;
    background: linear-gradient(145deg, var(--watermark-a), var(--watermark-b));
    border-radius: 4px;
  }

  .brand {
    display: flex; align-items: center; gap: 12px;
    font-family: "Cinzel", serif; font-weight: 600;
    color: var(--gold);
    letter-spacing: 1px;
  }
  .brand__mark {
    width: 14px; height: 14px; background: var(--gold); flex: none;
  }
  .brand__name { line-height: 1.15; text-transform: uppercase; }

  .card--front .brand {
    position: absolute; right: 44px; bottom: 70px;
    font-size: 22px;
  }

  .card--back .brand {
    position: absolute; left: 50%; top: 78px; transform: translateX(-50%);
    font-size: 28px; white-space: nowrap;
  }

  .details {
    position: absolute; left: 0; right: 0; top: 236px;
    display: flex; justify-content: center; align-items: stretch; gap: 26px;
  }
  .person { text-align: right; padding-top: 24px; }
  .person__name {
    font-family: "Cinzel", serif; font-weight: 500;
    font-size: 24px; color: var(--silver); letter-spacing: 1px;
  }
  .person__role {
    font-family: "Poppins", sans-serif; font-weight: 400;
    font-size: 15px; color: var(--gold); margin-top: 2px;
  }
  .divider { width: 1.5px; background: var(--gold); height: 104px; }
  .contacts { list-style: none; display: flex; flex-direction: column; gap: 8px; padding-top: 8px; }
  .contact {
    display: flex; align-items: center; gap: 9px;
    font-family: "Poppins", sans-serif; font-weight: 300;
    font-size: 14px; color: var(--silver);
  }
  .contact svg { width: 14px; height: 14px; flex: none; }
</style>
</head>
<body>
<main class="canvas">

  <section class="card card--front" aria-label="Card front">
    <div class="watermark" role="img" aria-label="Faint enlarged brand mark decoration"></div>
    <div class="brand">
      <span class="brand__mark"></span>
      <span class="brand__name">Renwick Tolliver<br>Construction</span>
    </div>
  </section>

  <section class="card card--back" aria-label="Card back">
    <div class="brand">
      <span class="brand__mark"></span>
      <span class="brand__name">Renwick Tolliver Construction</span>
    </div>

    <div class="details">
      <div class="person">
        <p class="person__name">LIONEL ASHBY</p>
        <p class="person__role">Managing Director</p>
      </div>
      <span class="divider"></span>
      <ul class="contacts">
        <li class="contact">
          <svg viewBox="0 0 24 24" aria-hidden="true"><path fill="#d9a531" d="M6.6 10.8a15.1 15.1 0 0 0 6.6 6.6l2.2-2.2a1 1 0 0 1 1-.25 11.4 11.4 0 0 0 3.6.57 1 1 0 0 1 1 1V20a1 1 0 0 1-1 1A17 17 0 0 1 3 4a1 1 0 0 1 1-1h3.5a1 1 0 0 1 1 1c0 1.25.2 2.45.57 3.57a1 1 0 0 1-.25 1z"/></svg>
          07822254961
        </li>
        <li class="contact">
          <svg viewBox="0 0 24 24" aria-hidden="true"><rect x="2" y="5" width="20" height="14" fill="#d9a531"/><path d="M2 5l10 8 10-8" fill="none" stroke="#111" stroke-width="1.8"/></svg>
          info@renwick-tolliver
        </li>
        <li class="contact">
          <svg viewBox="0 0 24 24" aria-hidden="true" fill="none" stroke="#d9a531" stroke-width="1.8"><circle cx="12" cy="12" r="9.5"/><ellipse cx="12" cy="12" rx="4" ry="9.5"/><path d="M2.5 12h19M4 7h16M4 17h16"/></svg>
          www.renwick-tolliver.co.uk
        </li>
      </ul>
    </div>
  </section>

</main>
</body>
</html>
```